Redesign Comparisson chart - make modern and effective

Use your imaginations to make a powerful distinction between KMV & other holistic modalities. There are 7 elements physical, mental, emotional, energetic, subconscious, superconscious and before and after testing.
We want it to be obvious that KMV is the only modality that works on all these elements simultaneously. We do not want to include any chakras as we want this information to be accepted by a wide range of people and belief systems.'

We want it to look simple but effective. Professional but powerful. We want KMV to stand out even of you eye just passed over i.
Updates

Hi everyone, thanks for your submissions so far. Basically what this image is meant to represent is a comparison chart between all the modalities There are 5 elements physical, mental, emotional, subconscious and superconscious. we want to reflect that KMV is the only modality that works on all these elements simultaneously. As we want the concept to be accepted and not considered woo woo, we want to steer away from chakras.

Target Market(s)

Professionals

Industry/Entity Type

Professional services

Font styles to use
Sans Serif
Other font styles liked:
• Poppins Monserratt

Colors
0094D4
00A9DD
6FCCEA
C7EBF8
E9F6FB

Requirements
Must have
• Clear/professional and clean look. Brand colours and logos. All typography and formats must be cohesive.
Nice to have
• More easy to read, different layout
Should not have
• Do not change the data just the way its presented. No chakras

```html
<!DOCTYPE html>
<html lang="en">
<head>
<meta charset="utf-8">
<title>KMV Modality Comparison Chart</title>
<link rel="stylesheet" href="https://fonts.googleapis.com/css2?family=Poppins:wght@500;600&family=Rubik:wght@400;500&family=Roboto:wght@400&display=swap">
<style>
  :root{
    --brand:#33b5e5;
    --band:#acdcf0;
    --panel:#e6f5fb;
    --column-dark:#0f78a6;
    --grid-line:#b3dbed;
    --ink:#1e1e1e;
    --physical:#e04141;
    --mental:#5bbcd9;
    --emotional:#5fae45;
    --energetic:#f7941d;
    --sub:#f2cf14;
    --super:#7c68ad;
    --testing:#dd6ea6;
  }
  *{box-sizing:border-box;margin:0;padding:0}
  html,body{width:1200px;height:912px;overflow:hidden;background:#fff}
  .canvas{position:relative;width:1200px;height:912px;background:#fff;font-family:"Roboto",sans-serif;color:var(--ink)}

  /* header */
  .brand{position:absolute;left:150px;top:26px;width:180px;text-align:center}
  .brand__name{font-family:"Rubik",sans-serif;font-weight:500;font-size:17px;line-height:22px;color:var(--brand);white-space:nowrap}
  .headline{position:absolute;left:340px;width:670px;top:10px;text-align:center}
  .headline__title{font-family:"Poppins",sans-serif;font-weight:600;font-size:18.5px;color:var(--brand);line-height:24px}
  .headline__lead{font-family:"Poppins",sans-serif;font-weight:500;font-size:10.2px;line-height:12.8px;margin-top:1px;color:var(--ink)}

  /* chart */
  .band{position:absolute;left:0;top:76px;width:1200px;height:691px;background:var(--band)}
  .panel{position:absolute;left:309px;top:91px;width:793px;height:667px;background:var(--panel);border-radius:10px 10px 0 0}
  .label-column{position:absolute;left:100px;top:131px;width:209px;height:627px;background:var(--column-dark);border-radius:10px 0 0 0}

  .col-heads{position:absolute;left:309px;top:91px;display:grid;grid-template-columns:repeat(7,106.4px);height:40px}
  .col-head{display:flex;align-items:center;justify-content:center;text-align:center;font-family:"Rubik",sans-serif;font-weight:500;font-size:13px;line-height:13.5px;border-right:1px solid var(--grid-line);border-bottom:1px solid var(--grid-line);margin-top:11px;padding-bottom:2px}
  .col-head:last-child{border-right:none}

  .rows{position:absolute;left:100px;top:131px;width:954px}
  .rows--lower{top:448px}
  .row{display:grid;grid-template-columns:209px repeat(7,106.4px);border-bottom:1px solid var(--grid-line)}
  .row:last-child{border-bottom:none}
  .row__label{font-family:"Rubik",sans-serif;font-size:12.6px;line-height:14.7px;color:#eaf6fb;text-transform:uppercase;padding-left:21px;display:flex;flex-direction:column;justify-content:center;white-space:nowrap}
  .cell{display:flex;align-items:center;justify-content:center;border-right:1px solid var(--grid-line)}
  .cell:last-child{border-right:none}

  .mark{width:9px;height:9px;transform:rotate(45deg);display:block}
  .mark--lg{width:17px;height:17px}
  .physical{background:var(--physical)} .mental{background:var(--mental)} .emotional{background:var(--emotional)}
  .energetic{background:var(--energetic)} .sub{background:var(--sub)} .super{background:var(--super)} .testing{background:var(--testing)}
  .t-physical{color:var(--physical)} .t-mental{color:var(--mental)} .t-emotional{color:var(--emotional)}
  .t-energetic{color:var(--energetic)} .t-sub{color:var(--sub)} .t-super{color:var(--super)} .t-testing{color:var(--testing)}

  .feature{position:absolute;left:59px;top:396px;width:1086px;height:52px;background:#fff;border-radius:7px;box-shadow:0 2px 6px rgba(0,0,0,.18);display:grid;grid-template-columns:250px repeat(7,106.4px);align-items:center}
  .feature__name{display:flex;align-items:center;gap:8px;padding-left:63px;font-family:"Rubik",sans-serif;font-size:12.6px;line-height:14.7px;color:var(--ink);text-transform:uppercase}
  .feature__dot{width:34px;height:34px;border-radius:50%;background:var(--brand);flex:none}
  .feature__cell{height:36px;display:flex;align-items:center;justify-content:center;border-left:1.5px solid var(--column-dark)}

  /* legend */
  .legend{position:absolute;top:776px;left:62px;display:grid;grid-template-columns:242px 242px 275px 268px;column-gap:16px}
  .legend__col:nth-child(3){margin-left:5px}
  .legend__item + .legend__item{margin-top:8px}
  .legend__head{display:flex;align-items:center;gap:9px;font-family:"Rubik",sans-serif;font-weight:500;font-size:13px;line-height:16px;text-transform:uppercase;margin-bottom:3px}
  .legend__head .mark{width:8px;height:8px}
  .legend__text{font-size:10.3px;line-height:12.7px;text-align:justify;color:#3a3a3a;hyphens:auto;-webkit-hyphens:auto}

  .footer-credit{position:absolute;left:64px;top:882px;display:flex;align-items:center;gap:7px;font-family:"Rubik",sans-serif;font-weight:500;color:var(--brand)}
  .footer-credit__name{font-size:12px;line-height:14px}
  .footer-credit__url{font-size:8px;line-height:12px;border-left:1px solid var(--brand);padding-left:7px}
</style>
</head>
<body>
<div class="canvas">

  <header>
    <div class="brand">
      <span class="brand__name">Keen Mind Vitality</span>
    </div>
    <div class="headline">
      <h1 class="headline__title">Choose KMV for Fast, Immediate and Powerful Results</h1>
      <p class="headline__lead">I must experience healing on all levels, I am not just a body. I want to learn how to heal myself, so I’m not dependent on others.<br>I want to release all my emotional and mental blocks, so I can be the best version of myself.</p>
    </div>
  </header>

  <div class="band"></div>
  <div class="panel"></div>
  <div class="label-column"></div>

  <div class="col-heads">
    <div class="col-head t-physical">PHYSICAL</div>
    <div class="col-head t-mental">MENTAL</div>
    <div class="col-head t-emotional">EMOTIONAL</div>
    <div class="col-head t-energetic">ENERGETIC</div>
    <div class="col-head t-sub">SUB<br>CONSCIOUS</div>
    <div class="col-head t-super">SUPER<br>CONSCIOUS</div>
    <div class="col-head t-testing">BEFORE &amp;<br>AFTER TESTING</div>
  </div>

  <div class="rows">
    <div class="row" style="height:88px">
      <div class="row__label"><span>Massage</span><span>Yoga</span><span>Natropathy</span><span>Ayurvedic Medicine</span><span>Western Medicine</span></div>
      <div class="cell"><i class="mark physical"></i></div><div class="cell"></div><div class="cell"></div><div class="cell"></div><div class="cell"></div><div class="cell"></div><div class="cell"></div>
    </div>
    <div class="row" style="height:26.5px">
      <div class="row__label">Psychic Intuitive</div>
      <div class="cell"><i class="mark physical"></i></div><div class="cell"><i class="mark mental"></i></div><div class="cell"></div><div class="cell"></div><div class="cell"></div><div class="cell"></div><div class="cell"></div>
    </div>
    <div class="row" style="height:26.5px">
      <div class="row__label">Family Constellation</div>
      <div class="cell"><i class="mark physical"></i></div><div class="cell"><i class="mark mental"></i></div><div class="cell"></div><div class="cell"><i class="mark energetic"></i></div><div class="cell"></div><div class="cell"></div><div class="cell"></div>
    </div>
    <div class="row" style="height:27px">
      <div class="row__label">Acupuncture</div>
      <div class="cell"><i class="mark physical"></i></div><div class="cell"></div><div class="cell"></div><div class="cell"><i class="mark energetic"></i></div><div class="cell"></div><div class="cell"></div><div class="cell"></div>
    </div>
    <div class="row" style="height:27px">
      <div class="row__label">Nutritional Healing</div>
      <div class="cell"><i class="mark physical"></i></div><div class="cell"></div><div class="cell"></div><div class="cell"></div><div class="cell"></div><div class="cell"></div><div class="cell"><i class="mark testing"></i></div>
    </div>
    <div class="row" style="height:27px">
      <div class="row__label">Chinese Medicine</div>
      <div class="cell"><i class="mark physical"></i></div><div class="cell"></div><div class="cell"></div><div class="cell"><i class="mark energetic"></i></div><div class="cell"></div><div class="cell"></div><div class="cell"><i class="mark testing"></i></div>
    </div>
    <div class="row" style="height:42px">
      <div class="row__label"><span>Kinesiology</span><span>Bowen Therapy</span></div>
      <div class="cell"><i class="mark physical"></i></div><div class="cell"></div><div class="cell"></div><div class="cell"></div><div class="cell"><i class="mark sub"></i></div><div class="cell"></div><div class="cell"><i class="mark testing"></i></div>
    </div>
  </div>

  <div class="rows rows--lower">
    <div class="row" style="height:27px">
      <div class="row__label">EFT</div>
      <div class="cell"><i class="mark physical"></i></div><div class="cell"><i class="mark mental"></i></div><div class="cell"></div><div class="cell"></div><div class="cell"><i class="mark sub"></i></div><div class="cell"></div><div class="cell"><i class="mark testing"></i></div>
    </div>
    <div class="row" style="height:27px">
      <div class="row__label">Chiropractic</div>
      <div class="cell"><i class="mark physical"></i></div><div class="cell"></div><div class="cell"></div><div class="cell"><i class="mark energetic"></i></div><div class="cell"><i class="mark sub"></i></div><div class="cell"></div><div class="cell"><i class="mark testing"></i></div>
    </div>
    <div class="row" style="height:42px">
      <div class="row__label"><span>Reiki</span><span>Crystal Healing</span></div>
      <div class="cell"></div><div class="cell"></div><div class="cell"></div><div class="cell"><i class="mark energetic"></i></div><div class="cell"></div><div class="cell"></div><div class="cell"></div>
    </div>
    <div class="row" style="height:27px">
      <div class="row__label">Energy Medicine</div>
      <div class="cell"></div><div class="cell"></div><div class="cell"></div><div class="cell"><i class="mark energetic"></i></div><div class="cell"></div><div class="cell"></div><div class="cell"><i class="mark testing"></i></div>
    </div>
    <div class="row" style="height:27px">
      <div class="row__label">Theta Healing</div>
      <div class="cell"></div><div class="cell"></div><div class="cell"></div><div class="cell"></div><div class="cell"><i class="mark sub"></i></div><div class="cell"><i class="mark super"></i></div><div class="cell"></div>
    </div>
    <div class="row" style="height:27px">
      <div class="row__label">Psychology</div>
      <div class="cell"></div><div class="cell"><i class="mark mental"></i></div><div class="cell"></div><div class="cell"></div><div class="cell"></div><div class="cell"></div><div class="cell"></div>
    </div>
    <div class="row" style="height:42px">
      <div class="row__label"><span>Mindfulness Meditation</span><span>Life Coaching</span></div>
      <div class="cell"></div><div class="cell"><i class="mark mental"></i></div><div class="cell"></div><div class="cell"></div><div class="cell"></div><div class="cell"></div><div class="cell"><i class="mark testing"></i></div>
    </div>
    <div class="row" style="height:43px">
      <div class="row__label"><span>Hypnotherapy</span><span>Inner Child Healing</span></div>
      <div class="cell"></div><div class="cell"><i class="mark mental"></i></div><div class="cell"></div><div class="cell"></div><div class="cell"><i class="mark sub"></i></div><div class="cell"></div><div class="cell"></div>
    </div>
    <div class="row" style="height:38px">
      <div class="row__label"><span>NLP</span><span>Timeline Therapy</span></div>
      <div class="cell"></div><div class="cell"><i class="mark mental"></i></div><div class="cell"></div><div class="cell"></div><div class="cell"><i class="mark sub"></i></div><div class="cell"></div><div class="cell"><i class="mark testing"></i></div>
    </div>
  </div>

  <div class="feature">
    <div class="feature__name"><span class="feature__dot"></span><span>Keen Mind<br>Vitality</span></div>
    <div class="feature__cell"><i class="mark mark--lg physical"></i></div>
    <div class="feature__cell"><i class="mark mark--lg mental"></i></div>
    <div class="feature__cell"><i class="mark mark--lg emotional"></i></div>
    <div class="feature__cell"><i class="mark mark--lg energetic"></i></div>
    <div class="feature__cell"><i class="mark mark--lg sub"></i></div>
    <div class="feature__cell"><i class="mark mark--lg super"></i></div>
    <div class="feature__cell"><i class="mark mark--lg testing"></i></div>
  </div>

  <section class="legend">
    <div class="legend__col">
      <div class="legend__item">
        <h3 class="legend__head t-physical"><i class="mark physical"></i>Physical</h3>
        <p class="legend__text">Most modalities, including, a western medicine, focus on and treat the physical body only. The KMV process enables you to engage in healing your own body during the session. There is no muscle testing, no hands-on healing and no herbal remedies or medicines.</p>
      </div>
    </div>
    <div class="legend__col">
      <div class="legend__item">
        <h3 class="legend__head t-mental"><i class="mark mental"></i>Mental</h3>
        <p class="legend__text">KMV enables you to use your own consciousness to self-heal. We don't give you advice or coaching, we allow your mind to heal itself.</p>
      </div>
      <div class="legend__item">
        <h3 class="legend__head t-energetic"><i class="mark energetic"></i>Energetic</h3>
        <p class="legend__text">Most modalities try to move the energy in your body for you. KMV enables and empowers you to do it yourself.</p>
      </div>
    </div>
    <div class="legend__col">
      <div class="legend__item">
        <h3 class="legend__head t-emotional"><i class="mark emotional"></i>Emotional</h3>
        <p class="legend__text">KMV is the only modality that engages your emotions on a physical level. Emotions get stuck in your body and can cause illness over time if left unchecked. KMV enables you you experience fast and powerful emotional releasing</p>
      </div>
      <div class="legend__item">
        <h3 class="legend__head t-super"><i class="mark super"></i>Superconscious</h3>
        <p class="legend__text">KMV is the only modality the enables you to access and heal your superconscious mind yourself.</p>
      </div>
    </div>
    <div class="legend__col">
      <div class="legend__item">
        <h3 class="legend__head t-sub"><i class="mark sub"></i>Subconscious</h3>
        <p class="legend__text">Some modalities, like Kinesiology, access your subcon&shy;scious through muscle testing. KMV empowers you to access your own subconscious and heal it yourself.</p>
      </div>
      <div class="legend__item">
        <h3 class="legend__head t-testing"><i class="mark testing"></i>Before &amp; After Testing</h3>
        <p class="legend__text">KMV is the only modality the enables you to provide before and after results, which are documented by us, and analysed by you with our help.</p>
      </div>
    </div>
  </section>

  <div class="footer-credit">
    <span class="footer-credit__name">Brightwell Studio</span>
    <span class="footer-credit__url">www.brightwellstudio.example</span>
  </div>

</div>
</body>
</html>
```